Business card for law firm

Need business card for new law firm. Think confident, authoritative, conservative, but not stuffy or old-fashioned.

Contact Information for Business Card

Content for card - logo (uploaded), plus the following:

Paul Whitcombe (larger font)
Managing Partner (larger font, but not as large as name)
Level 9, 7 Ferris Lane
Sydney NSW 2000
Main Tel 02 9364 2710
Direct Tel 02 8472 3159
Email paul@qvlegal.com.au
www.qvlegal.com.au

Letterhead design should include logo plus:
Level 9, 7 Ferris Lane
Sydney NSW 2000
Tel 02 8472 3159
www.qvlegal.com.au

```html
<!DOCTYPE html>
<html lang="en">
<head>
<meta charset="utf-8">
<title>Quayvale Legal – Business Card</title>
<link rel="stylesheet" href="https://fonts.googleapis.com/css2?family=Cinzel:wght@500&family=Open+Sans:wght@400&display=swap">
<style>
  :root {
    --backdrop: #9a9a9a;
    --paper: #ffffff;
    --navy: #001a57;
    --ink: #2b2b2b;
    --muted: #555555;
    --rule: #c9c9c9;
  }
  * { margin: 0; padding: 0; box-sizing: border-box; }
  html, body {
    width: 1200px; height: 900px; overflow: hidden;
    background: var(--backdrop);
  }
  .canvas { position: relative; width: 1200px; height: 900px; }

  .card {
    position: absolute;
    box-shadow: 2px 3px 5px rgba(0,0,0,0.45);
  }
  .card--front {
    left: 120px; top: 275px; width: 478px; height: 295px;
    background: var(--paper);
    border-radius: 0 52px 0 52px;
  }
  .card--back {
    left: 607px; top: 274px; width: 477px; height: 294px;
    background: var(--navy);
    border-radius: 52px 0 52px 0;
  }

  .firm-mark {
    position: absolute;
    display: flex; align-items: center; gap: 12px;
    font-family: "Cinzel", serif; font-weight: 500;
  }
  .firm-mark__square { display: block; flex: none; }
  .firm-mark__name { display: flex; flex-direction: column; align-items: center; line-height: 1; }
  .firm-mark__word { letter-spacing: 0.5px; }
  .firm-mark__sub { letter-spacing: 8px; margin-right: -8px; }

  .card--front .firm-mark { right: 28px; top: 336px; top: 60px; color: var(--ink); }
  .card--front .firm-mark__square { width: 40px; height: 40px; background: var(--navy); }
  .card--front .firm-mark__word { font-size: 30px; }
  .card--front .firm-mark__sub { font-size: 11px; margin-top: 6px; }

  .person { position: absolute; left: 25px; top: 153px; right: 28px; }
  .person__name {
    font-family: "Cinzel", serif; font-weight: 500;
    font-size: 18px; color: var(--navy); letter-spacing: 0.3px; line-height: 1.1;
  }
  .person__role {
    display: flex; align-items: center; gap: 4px;
    font-family: "Open Sans", sans-serif; font-size: 14px; color: var(--muted);
    line-height: 1.2;
  }
  .person__role::after { content: ""; flex: 1; height: 1px; background: var(--rule); margin-top: 2px; }

  .contact {
    position: absolute; left: 25px; top: 198px;
    list-style: none;
    font-family: "Open Sans", sans-serif; font-size: 14px; color: var(--ink);
  }
  .contact__item { display: flex; align-items: center; gap: 5px; height: 17.5px; }
  .contact__icon { width: 11px; height: 11px; fill: var(--navy); flex: none; }
  .contact__note { font-size: 12px; }

  .address {
    position: absolute; right: 28px; top: 234px;
    font-family: "Open Sans", sans-serif; font-size: 14px; color: var(--ink);
    font-style: normal; text-align: right; line-height: 17.5px;
  }

  .card--back .firm-mark {
    left: 0; right: 0; top: 78px;
    flex-direction: column; gap: 18px; color: var(--paper);
  }
  .card--back .firm-mark__square { width: 50px; height: 50px; background: var(--paper); }
  .card--back .firm-mark__word { font-size: 36px; }
  .card--back .firm-mark__sub { font-size: 12px; margin-top: 8px; letter-spacing: 9px; margin-right: -9px; }
</style>
</head>
<body>
<main class="canvas">

  <section class="card card--front" aria-label="Card front">
    <div class="firm-mark">
      <span class="firm-mark__square"></span>
      <span class="firm-mark__name">
        <span class="firm-mark__word">QUAYVALE</span>
        <span class="firm-mark__sub">LEGAL</span>
      </span>
    </div>

    <div class="person">
      <h1 class="person__name">PAUL WHITCOMBE</h1>
      <p class="person__role">Managing Partner</p>
    </div>

    <ul class="contact">
      <li class="contact__item">
        <svg class="contact__icon" viewBox="0 0 12 12"><path d="M1 4c0-2 2-3 5-3s5 1 5 3l-2 1-1-1.5H4L3 5zM2.5 6h7l1 4.5h-9z"/></svg>
        02 9364 2710
      </li>
      <li class="contact__item">
        <svg class="contact__icon" viewBox="0 0 12 12"><path d="M1 4c0-2 2-3 5-3s5 1 5 3l-2 1-1-1.5H4L3 5zM2.5 6h7l1 4.5h-9z"/></svg>
        02 8472 3159 <span class="contact__note">(DIRECT)</span>
      </li>
      <li class="contact__item">
        <svg class="contact__icon" viewBox="0 0 12 12"><path d="M0.5 2.5h11v7h-11z M1.5 3.5L6 7l4.5-3.5" fill="var(--navy)"/><path d="M1.2 3.2L6 6.8l4.8-3.6" stroke="#fff" stroke-width="1" fill="none"/></svg>
        paul@qvlegal.com.au
      </li>
      <li class="contact__item">
        <svg class="contact__icon" viewBox="0 0 12 12"><circle cx="6" cy="6" r="5.5"/><path d="M3 3.5l2 1-1 2 2 1-1 3M8 2l-1 2 2 1.5" stroke="#fff" stroke-width="0.9" fill="none"/></svg>
        www.qvlegal.com.au
      </li>
    </ul>

    <address class="address">
      Level 9, 7 Ferris Lane<br>
      Sydney NSW 2000
    </address>
  </section>

  <section class="card card--back" aria-label="Card back">
    <div class="firm-mark">
      <span class="firm-mark__square"></span>
      <span class="firm-mark__name">
        <span class="firm-mark__word">QUAYVALE</span>
        <span class="firm-mark__sub">LEGAL</span>
      </span>
    </div>
  </section>

</main>
</body>
</html>
```